Velk Partners Building Business Cards

We need a business card that reflects our business as "Solar Experts" in San Diego. Browse our website www.velkpartners.example our License needs to be displayed as "CSLB# 3867140" our phone number is (619) 555-0187

Save thousands on your electric bills and increase the value of your home while helping to protect the environment. Our solar installation experts will help you design the system that's right for you, using only the highest quality equipment that will look great and give you ideal performance. Our goal is to make you energy independent, and get your electric bill to 0.

Paul Osterby
(619) 555-0187
paul@velkpartners.example

Target Market(s)

Home owners in san diego looking for solar

Industry/Entity Type

Solar Energy

Contact Information for Business Card

Paul Osterby
(619) 555-0187
paul@velkpartners.example

Font styles to use
Other font styles liked:
• Use our logo font

Requirements
Must have
• License needs to be displayed as "CSLB# 3867140" our phone number is (619) 555-0187
Nice to have
• Real images of rooftop home solar in san diego
Should not have
• our business address

```html
<!DOCTYPE html>
<html lang="en">
<head>
<meta charset="utf-8">
<title>Velk Partners Building – Business Cards</title>
<link rel="stylesheet" href="https://fonts.googleapis.com/css2?family=Montserrat:wght@700;800&family=Open+Sans:wght@400;600&display=swap">
<style>
  :root {
    --navy: #1a3a73;
    --gold: #f5a800;
    --white: #ffffff;
    --ground: #e9ecee;
    --ink-soft: #dfe6f2;
  }
  * { box-sizing: border-box; margin: 0; padding: 0; }
  html, body { width: 1200px; height: 812px; overflow: hidden; }
  body {
    background: var(--ground);
    font-family: "Open Sans", Arial, sans-serif;
    display: flex;
    align-items: center;
    justify-content: center;
    gap: 40px;
  }
  .card {
    position: relative;
    width: 540px;
    height: 309px;
    overflow: hidden;
    box-shadow: 0 6px 18px rgba(0, 0, 0, 0.12);
  }

  /* Back of card */
  .card-back {
    background: var(--navy);
    color: var(--white);
    display: flex;
    flex-direction: column;
    align-items: center;
    justify-content: center;
    gap: 22px;
  }
  .brand-lockup {
    display: flex;
    align-items: center;
    gap: 14px;
  }
  .brand-dot {
    width: 34px;
    height: 34px;
    border-radius: 50%;
    background: var(--gold);
  }
  .brand-name {
    font-family: "Montserrat", Arial, sans-serif;
    font-weight: 800;
    font-size: 30px;
    letter-spacing: -0.5px;
    white-space: nowrap;
  }
  .card-back .brand-name { color: var(--white); }
  .back-url {
    font-size: 13px;
    letter-spacing: 2.5px;
    text-transform: uppercase;
    color: var(--ink-soft);
  }

  /* Front of card */
  .card-front { background: var(--white); }
  .front-wave {
    position: absolute;
    inset: 0;
    width: 100%;
    height: 100%;
  }
  .front-brand {
    position: absolute;
    left: 28px;
    top: 104px;
  }
  .front-brand .brand-name {
    color: var(--navy);
    font-size: 22px;
  }
  .holder {
    position: absolute;
    left: 32px;
    bottom: 24px;
  }
  .holder-name {
    font-family: "Montserrat", Arial, sans-serif;
    font-weight: 800;
    font-size: 21px;
    color: var(--gold);
    text-transform: uppercase;
    letter-spacing: 0.3px;
  }
  .holder-role {
    font-size: 14px;
    color: var(--white);
    text-transform: uppercase;
    margin-top: 2px;
  }
  .contact-list {
    position: absolute;
    right: 22px;
    top: 138px;
    list-style: none;
    text-align: right;
    color: var(--white);
    font-size: 12.5px;
    line-height: 1.65;
  }
  .contact-list li {
    display: flex;
    align-items: center;
    justify-content: flex-end;
    gap: 7px;
  }
  .contact-list svg { width: 11px; height: 11px; fill: var(--gold); flex: none; }
  .contact-list .no-icon { padding-right: 18px; }
</style>
</head>
<body>

  <section class="card card-back" aria-label="Business card back">
    <div class="brand-lockup">
      <span class="brand-dot"></span>
      <span class="brand-name">Velk Partners Building</span>
    </div>
    <p class="back-url">www.velkpartners.example</p>
  </section>

  <section class="card card-front" aria-label="Business card front">
    <svg class="front-wave" viewBox="0 0 540 309" preserveAspectRatio="none" aria-hidden="true">
      <path d="M0,309 L0,212 C200,212 290,168 340,108 C390,48 450,24 540,22 L540,309 Z" fill="#f5a800"/>
      <path d="M0,309 L0,216 C205,216 298,174 348,114 C398,56 458,32 540,30 L540,309 Z" fill="#1a3a73"/>
    </svg>

    <div class="front-brand brand-lockup">
      <span class="brand-name">Velk Partners Building</span>
    </div>

    <div class="holder">
      <p class="holder-name">Paul Osterby</p>
      <p class="holder-role">CEO/Founder</p>
    </div>

    <ul class="contact-list">
      <li class="no-icon">CSLB# 3867140</li>
      <li>(619) 555-0187
        <svg viewBox="0 0 24 24"><path d="M6.6 10.8a15 15 0 0 0 6.6 6.6l2.2-2.2a1 1 0 0 1 1-.25 11.4 11.4 0 0 0 3.6.57 1 1 0 0 1 1 1V20a1 1 0 0 1-1 1A17 17 0 0 1 3 4a1 1 0 0 1 1-1h3.5a1 1 0 0 1 1 1c0 1.25.2 2.45.57 3.6a1 1 0 0 1-.25 1z"/></svg>
      </li>
      <li>paul@velkpartners.example
        <svg viewBox="0 0 24 24"><path d="M2 5h20v14H2z M2 5l10 8 10-8" stroke="#1a3a73" stroke-width="1.6"/></svg>
      </li>
      <li>www.velkpartners.example
        <svg viewBox="0 0 24 24"><circle cx="12" cy="12" r="10"/></svg>
      </li>
    </ul>
  </section>

</body>
</html>
```